Create a modern, visually appealing flyer for Courier Service.

Copperfinch Freight Flyer Design Brief

Project Overview
Create a modern, visually appealing, front-and-back 8.5"x11" flyer for Copperfinch Freight to distribute to potential customers and vendors. The flyer should emphasize the company's expansive service area, reliability, technological capabilities, and broad service offerings.

Flyer Goals
Showcase Copperfinch's extensive regional coverage
Highlight core services, industries served, technology integration, certifications, and fleet capabilities
Convey reliability, modernity, and technology-driven professionalism
Encourage further interaction via a QR code (to be placed later by Copperfinch)

Visual Style & Branding
Color Scheme: Creative, modern colors that are vibrant and appealing, suitable for a technology-driven and professional logistics company.
Font Selection: Modern, clean, professional fonts; readability is essential. Update to Logo
Design Aesthetic: Balanced mix of minimalistic/clean, tech-driven/futuristic, and sophisticated/professional elements.
Background: Incorporate abstract graphic patterns or imagery reflecting logistics, technology, or mapping concepts (e.g., subtle maps, abstract roads).

Content Layout

Front Side

Company Name & Logo: Prominent but balanced

Service Area Map: Modern, stylized graphic highlighting North Dakota, Minnesota, Montana, South Dakota, and Northern Iowa, clearly marking major cities within these areas

Vehicle Graphic: Stylized graphic featuring a Halvek Porta van with the Copperfinch logo clearly visible

Certifications (as official logo badges): HIPAA, Hazmat/DOT, Radiopharmaceutical, TSA/IAC

Contact Information:

Copperfinch Freight, LLC

2964 41st Ave S, Suite 315, Fargo, ND 58104

www.cprfinch-example.com | dispatch@cprfinch-example.com

Back Side

Core Services (icons, modern style):

STAT/ASAP

Same Day

Next Day

Scheduled

Extended Drives

Onboard Courier / Hand Carry

Reverse Logistics

White Glove

Warehousing

Industries Served (icons matching services style):

Healthcare & Life Sciences

Pharmaceuticals

Retailers & E-Commerce

Distributors & Manufacturers

Educational Institutions

Legal & Financial Services

Food & Beverage

Technology & IT Companies

Government & Defense Companies

Technology Highlights:

Advanced Integration Capabilities

GPS Tracking

Live Vehicle Monitoring

Client Online Portal

Emphasis on Real-Time Tracking and seamless integrations

Fleet Capabilities:

Variety of Vehicles: Sedans, SUVs, Pickup Trucks, Cargo Vans, Sprinters, Straight Trucks

Key Vehicle Features: Liftgate capabilities prominently noted

Hub Locations: Clearly listed:

Fargo, ND

Bismarck, ND

Devils Lake, ND

Grand Forks, ND

Airport Codes Serviced:

FAR - Fargo, ND

BIS - Bismarck, ND

MOT - Minot, ND

GFK - Grand Forks, ND

XWA - Williston, ND

DIK - Dickinson, ND

DVL - Devils Lake, ND

JMS - Jamestown, ND

ABR - Aberdeen, SD

ATY - Watertown, SD

TRF - Thief River Falls, MN

BJI - Bemidji, MN

DTL - Detroit Lakes, MN

MSP - Minneapolis/St. Paul, MN

Design Elements

Use of modern graphics and custom icons for services and industries

Abstract patterns or technology-driven imagery

Professional but approachable tone, using concise, bulleted text organized clearly in sections

Avoid event-specific language; design for long-term general use

Imagery

Stylized, consistent iconography for services and industries

Stylized vehicle graphics (Halvek Porta van)

Custom graphics illustrating technology integrations (if official graphics unavailable)

Images from software provider's website: www.QuillbyteApps.com

Technical Requirements

8.5” x 11” flyer, double-sided

Digital-ready files provided for printing in-house; no specific print preferences necessary

High-resolution files suitable for both print and digital use

Deliverables

Editable source files (Adobe Illustrator, Photoshop, or InDesign)

High-resolution PDF for printing

Web-friendly PDF or digital version

This flyer should clearly communicate Copperfinch Freight’ commitment to reliable, technology-enhanced logistics solutions across the region, effectively engaging diverse audiences across key industries.

Concept 1: Modern Technology Hub
Front:
Dominated by an abstract, vibrant map illustrating the service region with key cities pinpointed.
The Copperfinch logo prominently at the top left, with stylized Halvek Porta van graphic subtly integrated onto the map roads.
Certifications as bold, minimalistic badges along the lower edge.
Crisp, clear contact info at bottom-right.
Back:
Split vertically into distinct sections, each clearly labeled with modern iconography for:
Core Services
Industries Served
Technology Highlights (with Quillbyte Apps visuals)
Fleet Capabilities (vehicle silhouettes/icons)
Airport codes listed in a streamlined table format along the bottom.
Abstract tech-pattern background (faded nodes, routes, or circuit-board style).

Concept 2: Futuristic Minimalism
Front:
Sleek, minimalist layout with a clean white or very light background.
Modern service area map using minimalist outlines and dots for major cities, in gradient blues or tech-inspired palette.
Prominent Copperfinch Freight logo at top-center.
Stylized Halvek Porta graphic appearing subtly at bottom corner.
Certifications displayed vertically as sleek, simplified logo badges.
Back:
Horizontally segmented sections for:
Core Services with clean, futuristic icons.
Industries Served section with matching sleek icons.
Technology Highlights, centered around Quillbyte Apps graphics and abstract integrated circuit imagery.
Fleet Capabilities detailed with simplified vehicle graphics.
Clearly defined hub locations and airport codes in a clean, structured list along the side.

Concept 3: Bold & Vibrant Professionalism
Front:
Bright, vivid color blocking with abstract geometric shapes referencing routes and logistics paths.
The service map as a central graphic, bold and modern, clearly marking key hubs.
A prominent stylized Halvek Porta van with Copperfinch logo creatively placed along the lower third of the flyer.
Certifications featured prominently within colored circular badges along the top or side.
Contact details neatly integrated at the bottom.
Back:
Dynamic grid layout clearly displaying:
Core Services and Industries Served with bold, vibrant icons.
Technology Highlights, clearly emphasized with screenshots or custom graphics from Quillbyte Apps.
Fleet Capabilities section featuring colorful vehicle silhouettes/icons.
Hub locations and airport codes clearly called out within visually appealing graphics or charts.
Rich abstract graphical background elements maintaining professional readability.

Designers should not use AI for designs.

Target Market(s)

Businesses Needing Courier Services

Font styles to use
Sans Serif

```html
<!DOCTYPE html>
<html lang="en">
<head>
<meta charset="utf-8">
<title>Copperfinch Freight, LLC — Flyer</title>
<link href="https://fonts.googleapis.com/css2?family=Rubik:wght@500;600;700;800;900&family=Montserrat:wght@400;500;600&display=swap" rel="stylesheet">
<style>
:root{
  --stage:#000000;
  --gold:#c4bd36;
  --gold-light:#dcd65a;
  --gold-deep:#a9a226;
  --brown:#4c3924;
  --brown-dark:#3a2b1a;
  --ink:#111111;
  --white:#ffffff;
  --cream:#f3f0dc;
  --cert-yellow:#f2e66a;
  --pin-red:#e41f1f;
  --pin-blue:#1b3fe4;
  --pin-green:#2fb34b;
  --pin-purple:#8b1ce2;
  --pin-orange:#e5491d;
}
*{box-sizing:border-box;margin:0;padding:0}
html,body{width:716px;height:1200px;overflow:hidden;background:var(--stage)}
body{position:relative;font-family:"Rubik",sans-serif;color:var(--ink)}
.page{
  position:absolute;left:154px;width:408px;height:527px;overflow:hidden;
  background:
    radial-gradient(circle at 78% 28%,rgba(255,250,150,.35),transparent 45%),
    radial-gradient(circle at 12% 70%,rgba(255,250,150,.22),transparent 40%),
    linear-gradient(160deg,var(--gold-light),var(--gold) 45%,var(--gold-deep));
}
.page--front{top:56px}
.page--back{top:625px}
.abs{position:absolute}

/* brand */
.brand{display:flex;align-items:center;gap:6px}
.brand__mark{width:22px;height:22px;border-radius:50%;background:var(--ink)}
.brand__name{font-weight:800;line-height:.95;color:var(--ink)}
.tagline{font-family:"Montserrat",sans-serif;letter-spacing:.22em;color:var(--ink)}

.front-brand{left:0;right:0;top:30px;justify-content:center}
.front-brand .brand__name{font-size:15px}
.front-tagline{left:0;right:0;top:71px;text-align:center;font-size:7px}
.hero-title{left:0;right:0;top:92px;text-align:center;font-weight:900;font-size:37px;line-height:.92;letter-spacing:-.5px}

.states{left:0;top:180px;width:100%;height:30px}
.state{position:absolute;top:15px;height:14px;border-radius:7px;color:var(--white);font-weight:700;font-size:8px;display:flex;align-items:center;justify-content:center}
.state__pin{position:absolute;top:-14px;left:50%;margin-left:-4px}
.state--mt{left:47px;width:49px;background:var(--pin-red)}
.state--nd{left:98px;width:65px;background:var(--pin-blue)}
.state--mn{left:167px;width:53px;background:var(--pin-green)}
.state--sd{left:226px;width:66px;background:var(--pin-purple)}
.state--ia{left:298px;width:67px;background:var(--pin-orange)}

.service-map{left:46px;top:222px;width:316px;height:150px;border-radius:30px 60px 40px 20px;
  background:linear-gradient(180deg,#f1f1f1,#d9d9d9);z-index:2}

.cert-band{left:0;top:354px;width:100%;height:111px;background:var(--brown);z-index:3}
.cert-title{left:27px;top:17px;color:var(--cert-yellow);font-weight:700;font-size:9px}
.cert{display:flex;align-items:center;gap:5px;color:var(--white);font-weight:700;font-size:7.5px;line-height:1.2;white-space:nowrap}
.cert__badge{width:24px;height:24px;border-radius:50%;background:var(--cream);border:2px solid #d8cfae;flex:none}
.cert--hipaa{left:27px;top:38px}
.cert--radio{left:94px;top:38px}
.cert--hazmat{left:27px;top:70px}
.cert--tsa{left:94px;top:70px}

.van{border-radius:24px 30px 14px 18px;
  background:linear-gradient(100deg,#5b4a33 0%,#d8d49a 35%,#ecebd0 60%,#bfa877 100%);z-index:4}
.van--front{left:196px;top:366px;width:192px;height:110px}

.footer{left:27px;right:20px;display:flex;align-items:center;justify-content:space-between}
.front-footer{top:481px}
.footer__company{font-weight:800;font-size:11px;line-height:1;text-transform:uppercase}
.footer__info{display:flex;gap:4px;font-weight:600;font-size:7.5px;line-height:1.35}
.footer__info svg{flex:none;margin-top:1px}
.footer__links{display:flex;flex-direction:column;gap:1px;font-weight:600;font-size:7.5px}
.footer__links span{display:flex;align-items:center;gap:3px}

/* back */
.services-frame{left:19px;top:27px;width:369px;height:77px;border:1px solid var(--brown);border-radius:12px}
.pill-title{left:95px;top:19px;width:217px;height:17px;border-radius:9px;background:var(--brown);color:var(--white);
  font-weight:700;font-size:10px;display:flex;align-items:center;justify-content:center;z-index:2}
.service{position:absolute;top:45px;width:40px;margin-left:-20px;text-align:center}
.service__icon{width:31px;height:31px;margin:0 auto;border-radius:50%;background:var(--white);border:3px solid var(--brown);display:flex;align-items:center;justify-content:center}
.service__label{margin-top:5px;font-weight:700;font-size:7px;line-height:1.2}

.section-title{font-weight:800;font-size:13px}
.industries-title{left:25px;top:118px}
.industries{left:0;top:143px;width:164px;height:165px;background:var(--brown);border-radius:0 8px 8px 0;padding:7px 14px 0 28px;list-style:none}
.industries li{color:var(--white);font-weight:700;font-size:7.8px;height:16.6px;line-height:16.6px;border-bottom:1px solid rgba(255,255,255,.12);white-space:nowrap}
.industries li:last-child{border-bottom:none}

.tech-title{left:183px;top:118px}
.tech{position:absolute;left:182px;width:220px;display:flex;gap:7px}
.tech__icon{width:30px;height:30px;border-radius:50%;background:var(--white);border:3px solid var(--brown);flex:none;margin-top:3px;display:flex;align-items:center;justify-content:center}
.tech__name{font-weight:700;font-size:8px}
.tech__text{font-family:"Montserrat",sans-serif;font-size:5.8px;line-height:1.25;margin-top:1px}

.vehicle-title{left:28px;top:322px}
.vehicle-band{left:0;top:341px;width:260px;height:44px;background:var(--brown)}
.vehicle-list{position:absolute;top:8px;list-style:none;color:var(--white);font-weight:700;font-size:7.5px;line-height:9.6px;white-space:nowrap}
.vehicle-list li::before{content:"";display:inline-block;width:4px;height:4px;border:1px solid var(--cert-yellow);border-radius:50%;margin-right:4px;vertical-align:middle}
.vehicle-list--a{left:31px}
.vehicle-list--b{left:112px}
.feature-badge{left:186px;top:308px;width:72px;height:72px;border-radius:50%;background:var(--white);border:3px solid var(--brown);z-index:4;
  display:flex;flex-direction:column;align-items:center;justify-content:center;font-weight:800;line-height:.95;text-align:center}
.feature-badge__kicker{font-size:7px;color:var(--brown)}
.feature-badge__main{font-size:9px;margin-top:3px}
.van--back{left:227px;top:328px;width:152px;height:79px;z-index:3}

.hub-title{left:27px;top:406px}
.hubs{left:129px;top:406px;height:17px;display:flex;border:1px solid var(--brown);border-radius:9px;background:var(--white);overflow:hidden}
.hubs span{font-family:"Montserrat",sans-serif;font-weight:500;font-size:7px;padding:0 4px;display:flex;align-items:center;border-right:1px solid var(--brown);white-space:nowrap}
.hubs span:last-child{border-right:none;padding-right:7px}
.hubs span:first-child{padding-left:6px}

.airports{left:26px;top:433px;width:359px;height:35px;border-radius:6px;background:var(--brown);display:flex;overflow:hidden}
.airports__label{width:96px;display:flex;align-items:center;gap:4px;padding-left:8px;color:var(--white);font-weight:800;font-size:8px;line-height:.95}
.airports__grid{flex:1;display:grid;grid-template-columns:repeat(7,1fr);grid-template-rows:1fr 1fr;background:var(--white);border-radius:6px}
.airports__grid span{display:flex;align-items:center;justify-content:center;font-family:"Montserrat",sans-serif;font-weight:500;font-size:10.5px;border-right:1px solid var(--brown);border-bottom:1px solid var(--brown)}
.airports__grid span:nth-child(7n){border-right:none}
.airports__grid span:nth-child(n+8){border-bottom:none}

.back-brand{left:28px;top:478px}
.back-brand .brand__mark{width:16px;height:16px}
.back-brand .brand__name{font-size:9px}
.back-tagline{left:27px;top:507px;font-size:4.5px;letter-spacing:.15em}
.back-footer{top:483px;left:142px}
</style>
</head>
<body>

<!-- FRONT -->
<section class="page page--front">
  <div class="abs brand front-brand">
    <span class="brand__mark"></span>
    <span class="brand__name">Copperfinch<br>Freight</span>
  </div>
  <p class="abs tagline front-tagline">Same Day &amp; Scheduled Deliveries</p>
  <h1 class="abs hero-title">Copperfinch<br>Freight, LLC</h1>

  <div class="abs states">
    <span class="state state--mt"><svg class="state__pin" width="8" height="11" viewBox="0 0 8 11"><path d="M4 0a4 4 0 0 1 4 4c0 3-4 7-4 7S0 7 0 4a4 4 0 0 1 4-4z" fill="#e41f1f"/><circle cx="4" cy="4" r="1.6" fill="#fff"/></svg>Montana</span>
    <span class="state state--nd"><svg class="state__pin" width="8" height="11" viewBox="0 0 8 11"><path d="M4 0a4 4 0 0 1 4 4c0 3-4 7-4 7S0 7 0 4a4 4 0 0 1 4-4z" fill="#1b3fe4"/><circle cx="4" cy="4" r="1.6" fill="#fff"/></svg>North Dakota</span>
    <span class="state state--mn"><svg class="state__pin" width="8" height="11" viewBox="0 0 8 11"><path d="M4 0a4 4 0 0 1 4 4c0 3-4 7-4 7S0 7 0 4a4 4 0 0 1 4-4z" fill="#2fb34b"/><circle cx="4" cy="4" r="1.6" fill="#fff"/></svg>Minnesota</span>
    <span class="state state--sd"><svg class="state__pin" width="8" height="11" viewBox="0 0 8 11"><path d="M4 0a4 4 0 0 1 4 4c0 3-4 7-4 7S0 7 0 4a4 4 0 0 1 4-4z" fill="#8b1ce2"/><circle cx="4" cy="4" r="1.6" fill="#fff"/></svg>South Dakota</span>
    <span class="state state--ia"><svg class="state__pin" width="8" height="11" viewBox="0 0 8 11"><path d="M4 0a4 4 0 0 1 4 4c0 3-4 7-4 7S0 7 0 4a4 4 0 0 1 4-4z" fill="#e5491d"/><circle cx="4" cy="4" r="1.6" fill="#fff"/></svg>Northern Iowa</span>
  </div>

  <div class="abs service-map" role="img" aria-label="Map of the United States with Montana, North Dakota, Minnesota, South Dakota and northern Iowa highlighted by coloured pins"></div>

  <div class="abs cert-band">
    <h2 class="abs cert-title">Our Certifications</h2>
    <div class="abs cert cert--hipaa"><span class="cert__badge"></span>HIPAA</div>
    <div class="abs cert cert--radio"><span class="cert__badge"></span>Radio<br>pharmaceutical</div>
    <div class="abs cert cert--hazmat"><span class="cert__badge"></span>Hazmat<br>/ DOT</div>
    <div class="abs cert cert--tsa"><span class="cert__badge"></span>TSA<br>/ IAC</div>
  </div>

  <div class="abs van van--front" role="img" aria-label="Branded Copperfinch Freight delivery van in cream, gold and brown livery"></div>

  <div class="abs footer front-footer">
    <p class="footer__company">Copperfinch<br>Freight, LLC</p>
    <p class="footer__info"><svg width="7" height="7" viewBox="0 0 10 10"><circle cx="5" cy="5" r="5" fill="#111"/><path d="M5 2 2.5 4.5V8h5V4.5z" fill="#c4bd36"/></svg><span>2964 41st Ave S, Suite 315<br>Fargo, ND 58104</span></p>
    <div class="footer__links">
      <span><svg width="7" height="7" viewBox="0 0 10 10"><circle cx="5" cy="5" r="4.3" fill="none" stroke="#111" stroke-width="1.2"/><path d="M1 5h8M5 1v8" stroke="#111"/></svg>www.cprfinch-example.com</span>
      <span><svg width="7" height="7" viewBox="0 0 10 10"><circle cx="5" cy="5" r="5" fill="#111"/><rect x="2.5" y="3.3" width="5" height="3.4" fill="none" stroke="#c4bd36" stroke-width=".8"/></svg>dispatch@cprfinch-example.com</span>
    </div>
  </div>
</section>

<!-- BACK -->
<section class="page page--back">
  <div class="abs services-frame"></div>
  <h2 class="abs pill-title">Copperfinch Freight Core Services</h2>

  <div class="service" style="left:52px"><div class="service__icon"><svg width="16" height="16" viewBox="0 0 16 16" fill="none" stroke="#111" stroke-width="1.3"><rect x="1.5" y="3" width="13" height="8" rx="4"/><path d="M5 11l-1 3 3-3"/></svg></div><p class="service__label">STAT /<br>ASAP</p></div>
  <div class="service" style="left:91px"><div class="service__icon"><svg width="16" height="16" viewBox="0 0 16 16" fill="none" stroke="#111" stroke-width="1.3"><circle cx="8" cy="8" r="6"/><path d="M8 4v4l3 2"/></svg></div><p class="service__label">Same<br>Day</p></div>
  <div class="service" style="left:129px"><div class="service__icon"><svg width="16" height="16" viewBox="0 0 16 16" fill="none" stroke="#111" stroke-width="1.3"><rect x="2" y="3" width="12" height="11" rx="1"/><path d="M2 6h12M5 10h6M9 8l2 2-2 2"/></svg></div><p class="service__label">Next<br>Day</p></div>
  <div class="service" style="left:167px"><div class="service__icon"><svg width="16" height="16" viewBox="0 0 16 16" fill="none" stroke="#111" stroke-width="1.3"><rect x="2" y="3" width="12" height="11" rx="1"/><path d="M2 6h12M5 9h1M8 9h1M11 9h1M5 12h1M8 12h1"/></svg></div><p class="service__label">Sche<br>duled</p></div>
  <div class="service" style="left:205px"><div class="service__icon"><svg width="16" height="16" viewBox="0 0 16 16" fill="none" stroke="#111" stroke-width="1.3"><rect x="5" y="5" width="6" height="6"/><path d="M2 2l3 3M14 2l-3 3M2 14l3-3M14 14l-3-3"/></svg></div><p class="service__label">Extended<br>Drives</p></div>
  <div class="service" style="left:243px"><div class="service__icon"><svg width="16" height="16" viewBox="0 0 16 16" fill="none" stroke="#111" stroke-width="1.3"><rect x="4" y="2" width="8" height="7"/><path d="M2 11h5l2 1h5"/></svg></div><p class="service__label">Hand<br>Carry</p></div>
  <div class="service" style="left:281px"><div class="service__icon"><svg width="16" height="16" viewBox="0 0 16 16" fill="none" stroke="#111" stroke-width="1.3"><path d="M13 8a5 5 0 1 1-2-4"/><path d="M11 1v3h3"/><rect x="6" y="6" width="4" height="4"/></svg></div><p class="service__label">Reverse<br>Logistics</p></div>
  <div class="service" style="left:319px"><div class="service__icon"><svg width="16" height="16" viewBox="0 0 16 16" fill="none" stroke="#111" stroke-width="1.3"><path d="M3 13V6l2-3 1 3h4l3 3v4z"/></svg></div><p class="service__label">White<br>Glove</p></div>
  <div class="service" style="left:359px"><div class="service__icon"><svg width="16" height="16" viewBox="0 0 16 16" fill="none" stroke="#111" stroke-width="1.3"><path d="M2 14V6l6-4 6 4v8"/><rect x="5" y="8" width="6" height="6"/></svg></div><p class="service__label">Ware<br>housing</p></div>

  <h2 class="abs section-title industries-title">Industries Served</h2>
  <ul class="abs industries">
    <li>Healthcare &amp; Life Sciences</li>
    <li>Pharmaceuticals</li>
    <li>Retail &amp; E-Commerce</li>
    <li>Distributors &amp; Manufacturers</li>
    <li>Educational Institutions</li>
    <li>Legal &amp; Financial Services</li>
    <li>Food &amp; Beverage</li>
    <li>Technology &amp; IT</li>
    <li>Government &amp; Defense</li>
  </ul>

  <h2 class="abs section-title tech-title">Technology Highlights</h2>
  <div class="tech" style="top:143px">
    <span class="tech__icon"><svg width="14" height="14" viewBox="0 0 14 14" fill="none" stroke="#111" stroke-width="1.2"><circle cx="3" cy="3" r="2"/><circle cx="11" cy="3" r="2"/><circle cx="3" cy="11" r="2"/><circle cx="11" cy="11" r="2"/><circle cx="7" cy="7" r="1.5"/></svg></span>
    <div><p class="tech__name">Advanced Integration Capabilities</p><p class="tech__text">Easily connect with your existing systems for streamlined operations. Our platform supports robust API and EDI integrations tailored to your workflow.</p></div>
  </div>
  <div class="tech" style="top:183px">
    <span class="tech__icon"><svg width="14" height="14" viewBox="0 0 14 14" fill="none" stroke="#111" stroke-width="1.2"><path d="M7 1a4 4 0 0 1 4 4c0 3-4 7-4 7S3 8 3 5a4 4 0 0 1 4-4z"/><circle cx="7" cy="5" r="1.4"/></svg></span>
    <div><p class="tech__name">Real-Time GPS Tracking &amp; Monitoring</p><p class="tech__text">Track every shipment live with pinpoint accuracy. Enjoy full visibility into driver location, route, and delivery status—updated in real time.</p></div>
  </div>
  <div class="tech" style="top:223px">
    <span class="tech__icon"><svg width="14" height="14" viewBox="0 0 14 14" fill="none" stroke="#111" stroke-width="1.2"><circle cx="5" cy="5" r="2"/><circle cx="10" cy="6" r="1.6"/><path d="M1 13c0-3 2-5 4-5s4 2 4 5M8 13c0-2 1-4 2-4s3 2 3 4"/></svg></span>
    <div><p class="tech__name">Client Online Portal</p><p class="tech__text">Access orders, track deliveries, and manage documents—all in one user-friendly dashboard. Available 24/7 to keep you in control.</p></div>
  </div>
  <div class="tech" style="top:264px">
    <span class="tech__icon"><svg width="14" height="14" viewBox="0 0 14 14" fill="none" stroke="#111" stroke-width="1.2"><circle cx="7" cy="7" r="2"/><circle cx="2" cy="2" r="1.3"/><circle cx="12" cy="2" r="1.3"/><circle cx="2" cy="12" r="1.3"/><circle cx="12" cy="12" r="1.3"/><path d="M3 3l2.5 2.5M11 3 8.5 5.5M3 11l2.5-2.5M11 11 8.5 8.5"/></svg></span>
    <div><p class="tech__name">Seamless Tech Integrations</p><p class="tech__text">We work with your tools, not against them. Our technology integrates effortlessly with CRMs, ERPs, and shipping platforms for a unified experience.</p></div>
  </div>

  <h2 class="abs section-title vehicle-title">Vehicle Types</h2>
  <div class="abs vehicle-band">
    <ul class="vehicle-list vehicle-list--a"><li>Sedans</li><li>SUVs</li><li>Pickup Trucks</li></ul>
    <ul class="vehicle-list vehicle-list--b"><li>Cargo Vans</li><li>Sprinters</li><li>Straight Trucks</li></ul>
  </div>
  <div class="abs van van--back" role="img" aria-label="Branded Copperfinch Freight delivery van with liftgate"></div>
  <div class="abs feature-badge">
    <span class="feature-badge__kicker">SPECIAL<br>FEATURE</span>
    <span class="feature-badge__main">LIFTGATE<br>EQUIPPED<br>VEHICLES</span>
  </div>

  <h2 class="abs section-title hub-title">Hub Locations</h2>
  <div class="abs hubs"><span>Fargo, ND</span><span>Bismarck, ND</span><span>Devils Lake, ND</span><span>Grand Forks, ND</span></div>

  <div class="abs airports">
    <div class="airports__label">
      <svg width="20" height="22" viewBox="0 0 20 22" fill="none" stroke="#f3f0dc" stroke-width="1.1"><path d="M5 21V8M3 8h4l-1-4H4zM1 21h18M9 15l9-4-1-1-4 1-3-2-1 1 2 2-3 1"/></svg>
      <span>AIRPORT<br>CODES<br>SERVICED</span>
    </div>
    <div class="airports__grid">
      <span>FAR</span><span>BIS</span><span>MOT</span><span>GFK</span><span>XWA</span><span>DIK</span><span>DVL</span>
      <span>JMS</span><span>ABR</span><span>ATY</span><span>TRF</span><span>BJI</span><span>DTL</span><span>MSP</span>
    </div>
  </div>

  <div class="abs brand back-brand">
    <span class="brand__mark"></span>
    <span class="brand__name">Copperfinch<br>Freight</span>
  </div>
  <p class="abs tagline back-tagline">Same Day &amp; Scheduled Deliveries</p>
  <div class="abs footer back-footer">
    <p class="footer__info"><svg width="7" height="7" viewBox="0 0 10 10"><circle cx="5" cy="5" r="5" fill="#111"/><path d="M5 2 2.5 4.5V8h5V4.5z" fill="#c4bd36"/></svg><span>2964 41st Ave S, Suite 315<br>Fargo, ND 58104</span></p>
    <div class="footer__links">
      <span><svg width="7" height="7" viewBox="0 0 10 10"><circle cx="5" cy="5" r="4.3" fill="none" stroke="#111" stroke-width="1.2"/><path d="M1 5h8M5 1v8" stroke="#111"/></svg>www.cprfinch-example.com</span>
      <span><svg width="7" height="7" viewBox="0 0 10 10"><circle cx="5" cy="5" r="5" fill="#111"/><rect x="2.5" y="3.3" width="5" height="3.4" fill="none" stroke="#c4bd36" stroke-width=".8"/></svg>dispatch@cprfinch-example.com</span>
    </div>
  </div>
</section>

</body>
</html>
```